Saint Brendan of the Fields banners

In need of two banners designed.
Product Details:
Imprint Area:
Banner stands: 2-33.5"W x 79"H (full color),

Product Size:
Two Banner Stands: 34"W x 83"H including base,
See attached for specifics

* We would like the logo and "Annual Fundraiser" added above the logo or on either side of the logo.
* The problem we were running in to was that "Annual" and "Fundraiser" are not equal in length.

Banner Stand
* This will talk about what the foundation is
Logo with "Annual Fundraiser" incorporated
*You can also visit our website www.sbfparishlakevale.org and go to the Education Foundation page for more info
Q: Who benefits from the foundation?
A: All Saint Brendan of the Fields(SBF) parishioners and local people looking to enhance their faith.
Q: What does the foundation fund?
A: All learning opportunities provided by the parish
*KINDLE and Adult Bible Studies
*Faith Formation (Nursery-12 th Grade)
*RCIA and Sacramental Prep
*Books and CD's distributed during Lent and Advent
*SBF Elementary and Middle School and Vacation Bible School
*Parish Library and Mission

Banner(Horizontal)
* This is going to talk about our needs. I'm thinking on the top we could write something like:
Q: How can I help?
A: Donate your time, talent, and treasure

* Then we have 2 ways they can help: Volunteer and Donate
VOLUNTEER
Time: Can you help plan before, during, or after the event?
Talent: Do you have a special talent that might help us plan?
creative: help with decor or ideas
tech savy: help with social media and website, putting together slideshow
marketing: help get the word out
sales and outgoing personality: help solicit donations
DONATE
Talent: Do you have a special talent that you may be able to use to make an auction item? Could you knit a blanket, create a piece of art, offer a service like personal training or a hair cut? Are you the hostess with the mostest and would like to donate a party for someone?
Treasure: Do you own a business that could donate services or goods? Do you have a vacation home you would be willing to rent out? Would you be willing to donate money towards the planning or to the foundation?

*If there is room across the bottom we could put "Food * Drinks * Band * Silent/Live Auction"

Target Market(s)

Parishioners of Church

Industry/Entity Type

Non Profit

Font styles to use
Serif
Sans Serif

Colors
3276b5
0455a3

Requirements
Must have
• * Generic enough to be used year after year
• * Easy to read and not to overwhelming
Nice to have
• I would love to see some graphics included. You can add to my choosen colors if you think colorful is better

```html
<!DOCTYPE html>
<html lang="en">
<head>
<meta charset="utf-8">
<title>Annual Fundraiser – How Can I Help</title>
<link href="https://fonts.googleapis.com/css2?family=Montserrat:wght@600;700;800&family=Raleway:ital,wght@0,700;0,800;1,700&family=Titan+One&display=swap" rel="stylesheet">
<style>
:root{
  --green:#8cc63f;
  --green-dark:#6fa82e;
  --green-light:#b4dc6e;
  --navy:#14305c;
  --blue:#1d75bc;
  --blue-light:#3a8fd0;
  --pink:#b5418f;
  --orange:#f3a51f;
  --yellow:#f5c518;
  --ink:#1b1b1b;
  --text:#2a2a2a;
  --white:#ffffff;
  --bg-top:#f2f3f5;
  --bg-bottom:#d8dce1;
}
*{margin:0;padding:0;box-sizing:border-box}
html,body{width:1200px;height:2972px;overflow:hidden}
body{background:linear-gradient(var(--bg-top),var(--bg-bottom));font-family:"Raleway",Arial,sans-serif;color:var(--text);position:relative}
.abs{position:absolute}
.header-bg{left:0;top:0}
.brand{left:40px;top:120px;width:400px;text-align:center;color:var(--white);font-family:"Montserrat",Arial,sans-serif;font-weight:700;font-size:44px;line-height:1.1}
.brand-mark{display:block;width:70px;height:70px;border-radius:50%;background:var(--white);margin:0 auto 24px}
.title{left:520px;top:230px;color:var(--white);font-family:"Montserrat",Arial,sans-serif;font-weight:800;line-height:1}
.title .annual{font-size:132px;letter-spacing:2px;display:block}
.title .fundraiser{font-size:86px;display:block;margin-top:6px}
.question{left:52px;top:668px}
.question-text{left:100px;top:690px;font-family:"Montserrat",Arial,sans-serif;font-weight:700;font-size:50px;color:var(--navy)}
.answer{left:360px;top:790px}
.answer-text{left:410px;top:830px;width:740px;font-family:"Montserrat",Arial,sans-serif;font-weight:700;font-size:44px;line-height:1.2;color:var(--navy)}
.section-title{font-family:"Titan One",Impact,sans-serif;font-size:84px;color:var(--ink);letter-spacing:1px;left:52px}
.icon-box{width:96px;height:96px;left:52px}
.sub-title{font-family:"Montserrat",Arial,sans-serif;font-weight:800;font-size:60px;left:190px}
.bullets{left:190px;font-weight:800;font-size:36px;line-height:1.5;color:var(--ink);white-space:nowrap}
.bullets .note{font-style:italic;font-weight:700}
.skill{width:300px;text-align:center;top:1500px}
.skill-circle{display:block;margin:0 auto}
.skill-name{margin-top:30px;font-family:"Montserrat",Arial,sans-serif;font-weight:800;font-size:34px;line-height:1.05;color:var(--ink)}
.skill-desc{font-style:italic;font-weight:700;font-size:27px;line-height:1.2;color:var(--text)}
.col-bar{left:52px;width:96px}
.donate-list{left:190px;font-weight:800;font-size:36px;line-height:1.45;color:var(--ink);white-space:nowrap}
.donate-list p{margin-bottom:24px}
</style>
</head>
<body>

<svg class="abs header-bg" width="1200" height="700" viewBox="0 0 1200 700">
  <rect x="0" y="0" width="1200" height="470" fill="var(--green)"/>
  <path d="M0 460 L1200 400 L1200 640 C900 620 500 610 0 660 Z" fill="var(--navy)"/>
  <path d="M0 610 C400 560 800 585 1200 600 L1200 640 C900 620 500 610 0 660 Z" fill="var(--blue-light)"/>
</svg>

<div class="abs brand"><span class="brand-mark"></span>Saint Brendan<br>of the Fields</div>

<div class="abs title"><span class="annual">ANNUAL</span><span class="fundraiser">FUNDRAISER</span></div>

<svg class="abs question" width="720" height="110" viewBox="0 0 720 110">
  <polygon points="610,8 720,0 700,80 620,88" fill="var(--green-dark)"/>
  <rect x="0" y="10" width="660" height="88" fill="var(--yellow)"/>
</svg>
<div class="abs question-text">Q: How can I help?</div>

<svg class="abs answer" width="800" height="230" viewBox="0 0 800 230">
  <polygon points="30,0 260,10 250,40 20,40" fill="var(--green-light)"/>
  <rect x="30" y="30" width="760" height="190" fill="var(--green)"/>
</svg>
<div class="abs answer-text">A: Sacrificial giving! Share your TIME, TALENT, and TREASURE</div>

<div class="abs section-title" style="top:1040px">VOLUNTEER</div>

<svg class="abs icon-box" style="top:1152px" viewBox="0 0 96 96">
  <rect width="96" height="96" fill="var(--green)"/>
  <circle cx="48" cy="48" r="28" fill="none" stroke="var(--white)" stroke-width="6"/>
  <path d="M48 30 V48 H62" fill="none" stroke="var(--white)" stroke-width="6" stroke-linecap="round"/>
</svg>
<div class="abs sub-title" style="top:1140px;color:var(--green)">TIME:</div>
<div class="abs bullets" style="top:1205px">
  · Are you available to plan?<br>
  · Could you help set up?<br>
  <span class="note">We need help during the event. Help wrap up the event.</span>
</div>

<svg class="abs icon-box" style="top:1356px" viewBox="0 0 96 96">
  <rect width="96" height="96" fill="var(--blue)"/>
  <circle cx="40" cy="40" r="14" fill="var(--white)"/>
  <path d="M16 80 C16 58 64 58 64 80 Z" fill="var(--white)"/>
  <polygon points="72,14 76,24 86,24 78,30 81,40 72,34 63,40 66,30 58,24 68,24" fill="var(--white)"/>
</svg>
<div class="abs sub-title" style="top:1345px;color:var(--blue)">TALENT:</div>
<div class="abs bullets" style="top:1415px">Are you creative? Want to help with decor or ideas?</div>

<div class="abs skill" style="left:0">
  <svg class="skill-circle" width="150" height="150" viewBox="0 0 150 150">
    <circle cx="75" cy="75" r="75" fill="var(--blue-light)"/>
    <line x1="100" y1="42" x2="58" y2="92" stroke="var(--white)" stroke-width="8" stroke-linecap="round"/>
    <ellipse cx="50" cy="102" rx="12" ry="8" fill="var(--white)" transform="rotate(-45 50 102)"/>
  </svg>
  <div class="skill-name">CREATIVE:</div>
  <div class="skill-desc">help with decor<br>or ideas</div>
</div>

<div class="abs skill" style="left:303px">
  <svg class="skill-circle" width="150" height="150" viewBox="0 0 150 150">
    <circle cx="75" cy="75" r="75" fill="var(--pink)"/>
    <rect x="38" y="42" width="74" height="50" rx="4" fill="none" stroke="var(--white)" stroke-width="6"/>
    <rect x="68" y="92" width="14" height="14" fill="var(--white)"/>
    <rect x="54" y="104" width="42" height="6" fill="var(--white)"/>
  </svg>
  <div class="skill-name">TECH SAVY:</div>
  <div class="skill-desc">Help us with the<br>website, program, or<br>multi media.</div>
</div>

<div class="abs skill" style="left:608px">
  <svg class="skill-circle" width="150" height="150" viewBox="0 0 150 150">
    <circle cx="75" cy="75" r="75" fill="var(--green)"/>
    <polygon points="44,64 96,40 96,110 44,86" fill="var(--white)"/>
    <rect x="36" y="64" width="12" height="22" fill="var(--white)"/>
    <rect x="52" y="86" width="10" height="22" fill="var(--white)"/>
  </svg>
  <div class="skill-name">MARKETING:</div>
  <div class="skill-desc">Like to spread the<br>word? Come on board<br>and help us with our<br>social media, signage,<br>and marketing.</div>
</div>

<div class="abs skill" style="left:910px">
  <svg class="skill-circle" width="150" height="150" viewBox="0 0 150 150">
    <circle cx="75" cy="75" r="75" fill="var(--navy)"/>
    <circle cx="75" cy="56" r="10" fill="var(--white)"/>
    <circle cx="48" cy="66" r="8" fill="var(--white)"/>
    <circle cx="102" cy="66" r="8" fill="var(--white)"/>
    <rect x="62" y="70" width="26" height="30" rx="6" fill="var(--white)"/>
    <rect x="38" y="78" width="20" height="24" rx="5" fill="var(--white)"/>
    <rect x="92" y="78" width="20" height="24" rx="5" fill="var(--white)"/>
  </svg>
  <div class="skill-name">SALES AND<br>OUTGOING<br>PERSONALITY:</div>
  <div class="skill-desc">help solicit donations</div>
</div>

<div class="abs section-title" style="top:1905px">DONATE</div>

<div class="abs col-bar" style="top:2043px;height:300px;background:var(--pink)"></div>
<svg class="abs icon-box" style="top:2043px" viewBox="0 0 96 96">
  <circle cx="40" cy="40" r="14" fill="var(--white)"/>
  <path d="M16 80 C16 58 64 58 64 80 Z" fill="var(--white)"/>
  <polygon points="72,14 76,24 86,24 78,30 81,40 72,34 63,40 66,30 58,24 68,24" fill="var(--white)"/>
</svg>
<div class="abs sub-title" style="top:2040px;color:var(--pink)">TALENT:</div>
<div class="abs donate-list" style="top:2120px">
  <p>· Do you have a special talent that you may be<br>&nbsp;&nbsp;able to use to make an auction item?</p>
  <p>· Could you knit a blanket, create a piece of art,<br>&nbsp;&nbsp;offer a service like personal training or a hair cut?</p>
  <p>· Are you the hostess with the mostest and<br>&nbsp;&nbsp;would like to donate a party for someone?</p>
</div>

<div class="abs col-bar" style="top:2560px;height:412px;background:var(--orange)"></div>
<svg class="abs icon-box" style="top:2560px" viewBox="0 0 96 96">
  <rect x="20" y="30" width="56" height="42" fill="none" stroke="var(--white)" stroke-width="5"/>
  <line x1="20" y1="44" x2="76" y2="44" stroke="var(--white)" stroke-width="5"/>
  <rect x="42" y="40" width="12" height="12" fill="var(--white)"/>
</svg>
<div class="abs sub-title" style="top:2556px;color:var(--orange)">TREASURE:</div>
<div class="abs donate-list" style="top:2632px;line-height:1.35">
  <p style="margin-bottom:14px">· Do you own a business that could donate ser-<br>&nbsp;&nbsp;vices or goods?</p>
  <p style="margin-bottom:14px">· Do you have a vacation home you would be<br>&nbsp;&nbsp;willing to rent out?</p>
  <p style="margin-bottom:0">· Would you be willing to donate money<br>&nbsp;&nbsp;towards the planning or to the foundation?</p>
</div>

</body>
</html>
```